New design for www.TrimTable.com

On TrimTable you can find & book your hairdresser. TrimTable is the biggest platform in the Netherlands.

- The design should be a responcive design
- Should be able to go global, should fit in perfectly between all the big booking platforms like stayvo, ridlo etc,
- Should have te result of more bookings. :)
- We are ‘only’ asking a beautiful design, not a technical solution.
- We need a homepage (https://trimtable.com/), search resultpage ((https://trimtable.com/kapper/amsterdam/#), salonpage (https://trimtable.com/kapper/vorden/lumo-for-hair/), about us page (https://trimtable.com/aboutus/), for the hairdresser info page (https://trimtable.com/kapper/), login/register page (https://trimtable.com/account/signin/).

- On the page of the hairdresser there is a dynamic part. The part where you create your appointment. Please take a look at this part too after you choose your treatment (behandeling), employee (medewerker), Date (datum) and time (tijd). The part that you see after this, is the part where you fill in your data as a consumer.

I've added more logo's but mostly we use the green color.

A few of our competitors: www.plumsalo.com, www.korifex.com

Target Market(s)

All consumers

Industry/Entity Type

Hair And Beauty

Number of Pages Required

5+ page

Font styles to use
Sans Serif

Colors
abd036
c3c3c3
757575

Requirements
Must have
• Responsive
• We did an A/B test with the homepage. It turns out that option B works better then option A (take a look at the uploaded pictures). So what we need on the homepage: The USP's with the green checkboxes, The search button needs to by dynamic (changes for example from light green to dark green so you can see you can click it) The call to action sentence Zoek & Vind je kapsalon, the searchfield and searchbutton should be seperated.
Nice to have
• The style that we like is the flat design style. The website should be simple, clean and it should feel a bit like a luxury thing. Because an appointment with the hairdresser can be a real treat and luxury moment for yourself.
• The luxury feeling and flat design that is in the www.ridlo.com website is really nice for example. But then it has to be a bit more light and not so black and dark.

```html
<!DOCTYPE html>
<html lang="en">
<head>
<meta charset="utf-8">
<title>TrimTable – Find &amp; Book Your Hairdresser</title>
<link href="https://fonts.googleapis.com/css2?family=Lato:ital,wght@0,300;0,400;0,700;1,300;1,400&display=swap" rel="stylesheet">
<style>
:root{
  --green:#abd036;
  --green-dark:#93b527;
  --orange:#f47b20;
  --ink:#2b2b2b;
  --grey:#757575;
  --grey-light:#c3c3c3;
  --paper:#f2f2f2;
  --footer:#2a2a2a;
  --white:#ffffff;
}
*{margin:0;padding:0;box-sizing:border-box}
html,body{width:1200px;height:3020px;overflow:hidden}
body{font-family:"Lato",Arial,sans-serif;color:var(--ink);background:var(--white);position:relative}
section,header,nav,footer{position:absolute;left:0;width:1200px}

/* top bar */
.topbar{top:0;height:60px;background:var(--white)}
.brand{position:absolute;left:40px;top:13px;display:flex;align-items:center;gap:10px}
.brand-square{width:34px;height:34px;background:var(--green);border-radius:4px}
.brand-name{font-size:24px;font-weight:700;color:var(--green)}
.book-btn{position:absolute;left:540px;top:13px;width:240px;height:34px;background:var(--orange);color:var(--white);font-size:14px;font-weight:700;display:flex;align-items:center;justify-content:center;gap:8px;border-radius:3px}
.account{position:absolute;top:14px;font-size:11px;color:var(--grey);line-height:15px}
.account b{color:var(--orange);font-weight:700;display:block}
.account.new{left:900px}
.account.have{left:990px}
.flag{position:absolute;left:1100px;top:20px;width:24px;height:16px;border:1px solid var(--grey-light)}
.flag i{display:block;height:33.33%}

/* nav */
.mainnav{top:60px;height:32px;background:var(--green);display:flex;justify-content:center;gap:0}
.mainnav a{display:block;padding:0 36px;line-height:32px;font-size:12px;font-weight:700;color:var(--white);text-decoration:none;text-transform:uppercase;letter-spacing:.5px}
.mainnav a.active{background:var(--orange)}

/* hero */
.hero{top:92px;height:528px}
.hero-photo{position:absolute;inset:0;background:linear-gradient(90deg,#1c1c1c 0%,#262320 38%,#5c4530 62%,#b38a5c 82%,#d8b585 100%)}
.hero-title{position:absolute;left:100px;top:190px;width:470px;color:var(--orange);font-size:30px;font-weight:300;line-height:40px;text-align:center}
.hero-title em{font-style:italic;color:var(--white);font-weight:400}
.hero-search{position:absolute;left:135px;top:380px;display:flex;gap:6px}
.hero-search .field{width:300px;height:38px;background:var(--white);font-size:14px;color:var(--grey);padding:0 12px;line-height:38px}
.hero-search .go{width:42px;height:38px;background:var(--green);display:flex;align-items:center;justify-content:center}

/* stats */
.stats{top:620px;height:360px;background:var(--white)}
.stats-title{position:absolute;top:50px;width:100%;text-align:center;font-size:28px;font-weight:300;color:var(--green)}
.stats-title em{font-style:italic}
.pin{position:absolute;top:130px;width:90px;text-align:center}
.pin svg{display:block;margin:0 auto}
.pin .num{position:absolute;top:34px;left:0;width:90px;color:var(--white);font-size:16px;font-weight:700}
.pin .label{margin-top:18px;font-size:13px;color:var(--ink);line-height:18px}

/* app band */
.app{top:980px;height:360px;background:#eeeeee}
.app-phones{position:absolute;left:130px;top:30px;width:380px;height:300px;background:linear-gradient(160deg,#e6e6e6,#bfbfbf);border-radius:6px}
.app-band{position:absolute;left:0;top:0}
.app-text{position:absolute;left:680px;top:70px;width:440px;color:var(--white)}
.app-text h2{font-size:26px;font-weight:400;line-height:34px}
.app-text p{margin-top:18px;font-size:15px;line-height:23px}
.app-btn{display:inline-block;margin-top:22px;background:var(--orange);color:var(--white);font-size:13px;font-weight:700;padding:11px 24px;border-radius:3px}

/* steps */
.steps{top:1340px;height:480px;background:var(--white)}
.steps-title{position:absolute;top:50px;width:100%;text-align:center;font-size:28px;font-weight:300;color:var(--orange)}
.steps-sub{position:absolute;top:90px;width:100%;text-align:center;font-size:22px;font-style:italic;color:var(--ink)}
.steps-lines{position:absolute;left:0;top:0}
.step-label{position:absolute;width:200px;text-align:center;font-size:14px;line-height:19px;color:var(--ink)}
.steps-btn{position:absolute;left:510px;top:405px;width:180px;height:40px;background:var(--ink);color:var(--white);font-size:12px;font-weight:700;text-align:center;line-height:40px;letter-spacing:.5px}

/* testimonials */
.clients{top:1820px;height:440px;background:var(--paper)}
.clients-title{position:absolute;top:40px;width:100%;text-align:center;font-size:28px;font-weight:300;color:var(--green)}
.clients-sub{position:absolute;top:82px;width:100%;text-align:center;font-size:15px;color:var(--grey)}
.avatar{position:absolute;left:555px;top:130px;width:90px;height:90px;border-radius:50%;background:linear-gradient(160deg,#d9d9d9,#9a9a9a);border:4px solid var(--white)}
.client-name{position:absolute;top:248px;width:100%;text-align:center;font-size:17px;font-weight:700;color:var(--green)}
.quote{position:absolute;left:190px;top:285px;width:820px;text-align:center;font-size:14px;font-style:italic;line-height:22px;color:var(--grey)}
.quote-mark{position:absolute;top:268px;font-size:60px;color:var(--grey-light);font-family:Georgia,serif;line-height:60px}
.arrow{position:absolute;top:200px}

/* booking form */
.booking{top:2260px;height:520px}
.booking-photo{position:absolute;inset:0;background:linear-gradient(120deg,#d7d7d7 0%,#ececec 45%,#f7f7f7 100%)}
.form-card{position:absolute;left:120px;top:50px;width:560px;height:420px;background:rgba(244,235,218,.92);padding:24px}
.form-row{display:flex;gap:16px;margin-bottom:16px}
.input{flex:1;height:38px;background:var(--white);border:1px solid #e0d7c4;font-size:13px;color:var(--grey);padding:0 12px;line-height:36px;display:flex;justify-content:space-between;align-items:center}
.input.area{height:80px;align-items:flex-start}
.submit{display:block;margin:8px auto 0;width:190px;height:38px;background:var(--green);color:var(--white);font-size:12px;font-weight:700;text-align:center;line-height:38px;letter-spacing:.5px}
.booking-cta{position:absolute;left:730px;top:175px;width:400px}
.booking-cta h3{font-size:28px;font-weight:300;color:var(--orange)}
.booking-cta p{margin-top:14px;font-size:24px;font-style:italic;line-height:33px;color:var(--ink)}

/* footer */
.site-footer{top:2780px;height:240px;background:var(--footer);color:#cfcfcf}
.fcol{position:absolute;top:30px;font-size:12px;line-height:20px}
.fcol h4{font-size:15px;color:var(--white);font-weight:400;margin-bottom:12px}
.fcol .row{display:flex;gap:8px;align-items:flex-start;margin-bottom:6px}
.fcol b{color:var(--white);font-weight:700}
.fcol .phone{font-size:16px;color:var(--white)}
.fbrand{position:absolute;left:920px;top:40px;display:flex;align-items:center;gap:8px}
.fbrand .brand-square{width:28px;height:28px}
.fbrand span{font-size:20px;font-weight:700;color:var(--grey)}
.socials{position:absolute;left:950px;top:95px;display:flex;gap:6px}
.socials i{width:24px;height:24px;background:#8a8a8a;border-radius:3px}
.copy{position:absolute;left:920px;top:132px;width:200px;text-align:center;font-size:11px;line-height:16px;color:#a5a5a5}
</style>
</head>
<body>

<header class="topbar">
  <div class="brand"><span class="brand-square"></span><span class="brand-name">TrimTable</span></div>
  <div class="book-btn">
    <svg width="16" height="16" viewBox="0 0 16 16"><rect x="1.5" y="3" width="13" height="11.5" fill="none" stroke="#fff" stroke-width="1.5"/><line x1="1.5" y1="6.5" x2="14.5" y2="6.5" stroke="#fff" stroke-width="1.5"/><line x1="5" y1="1" x2="5" y2="4" stroke="#fff" stroke-width="1.5"/><line x1="11" y1="1" x2="11" y2="4" stroke="#fff" stroke-width="1.5"/></svg>
    Book An Appointment
  </div>
  <div class="account new">New User?<b>Sign Up</b></div>
  <div class="account have">Have Account?<b>Sign In</b></div>
  <div class="flag"><i style="background:#ae1c28"></i><i style="background:#fff"></i><i style="background:#21468b"></i></div>
</header>

<nav class="mainnav">
  <a class="active" href="#">Home</a>
  <a href="#">About Us</a>
  <a href="#">How It Works</a>
  <a href="#">Testimonials</a>
  <a href="#">Contact Us</a>
</nav>

<section class="hero">
  <div class="hero-photo" role="img" aria-label="Photo of a woman with long wavy blonde hair on a dark background"></div>
  <h1 class="hero-title">The Greatest Hairdresser Bookings Site In <em>The Netherlands With 542 Hairdressers.</em></h1>
  <div class="hero-search">
    <div class="field">Salon Naam Post Code</div>
    <div class="go"><svg width="18" height="18" viewBox="0 0 18 18"><circle cx="7.5" cy="7.5" r="5.5" fill="none" stroke="#fff" stroke-width="2"/><line x1="11.5" y1="11.5" x2="16" y2="16" stroke="#fff" stroke-width="2.5" stroke-linecap="round"/></svg></div>
  </div>
</section>

<section class="stats">
  <h2 class="stats-title">Last appointment on <em>October 16, 2015 at 13:54</em></h2>
  <div class="pin" style="left:163px"><svg width="80" height="110" viewBox="0 0 80 110"><path d="M40 108 C30 88 2 66 2 40 A38 38 0 0 1 78 40 C78 66 50 88 40 108Z" fill="#abd036"/></svg><span class="num">121.22</span><div class="label">Salons</div></div>
  <div class="pin" style="left:355px"><svg width="80" height="110" viewBox="0 0 80 110"><path d="M40 108 C30 88 2 66 2 40 A38 38 0 0 1 78 40 C78 66 50 88 40 108Z" fill="#abd036"/></svg><span class="num">123</span><div class="label">Treatments For<br>Booking</div></div>
  <div class="pin" style="left:555px"><svg width="80" height="110" viewBox="0 0 80 110"><path d="M40 108 C30 88 2 66 2 40 A38 38 0 0 1 78 40 C78 66 50 88 40 108Z" fill="#abd036"/></svg><span class="num">240.78</span><div class="label">Agreements</div></div>
  <div class="pin" style="left:751px"><svg width="80" height="110" viewBox="0 0 80 110"><path d="M40 108 C30 88 2 66 2 40 A38 38 0 0 1 78 40 C78 66 50 88 40 108Z" fill="#abd036"/></svg><span class="num">103.3</span><div class="label">Hairdressers<br>Booking</div></div>
  <div class="pin" style="left:943px"><svg width="80" height="110" viewBox="0 0 80 110"><path d="M40 108 C30 88 2 66 2 40 A38 38 0 0 1 78 40 C78 66 50 88 40 108Z" fill="#abd036"/></svg><span class="num">986</span><div class="label">Reliable Reviews</div></div>
</section>

<section class="app">
  <div class="app-phones" role="img" aria-label="Two smartphones showing the TrimTable booking app"></div>
  <svg class="app-band" width="1200" height="360" viewBox="0 0 1200 360"><polygon points="640,0 1200,0 1200,360 580,360" fill="#abd036"/></svg>
  <div class="app-text">
    <h2>All The Hairdressers Of Netherlands In Your Pocket ?</h2>
    <p>Download The Andora App And Always Find A Place To Make A Good Hairday Of...</p>
    <span class="app-btn">Download Andora APP</span>
  </div>
</section>

<section class="steps">
  <h2 class="steps-title">It's Very Easy 3 Step Process!</h2>
  <p class="steps-sub">Here's How It Works...</p>
  <svg class="steps-lines" width="1200" height="480" viewBox="0 0 1200 480">
    <line x1="80" y1="290" x2="153" y2="290" stroke="#f47b20" stroke-width="2"/>
    <line x1="263" y1="282" x2="545" y2="188" stroke="#f47b20" stroke-width="2"/>
    <line x1="655" y1="188" x2="937" y2="282" stroke="#f47b20" stroke-width="2"/>
    <line x1="1047" y1="290" x2="1120" y2="290" stroke="#f47b20" stroke-width="2"/>
    <circle cx="80" cy="290" r="4" fill="#f47b20"/><circle cx="1120" cy="290" r="4" fill="#f47b20"/>
    <circle cx="208" cy="290" r="52" fill="#fff" stroke="#f47b20" stroke-width="4"/>
    <circle cx="600" cy="180" r="52" fill="#fff" stroke="#f47b20" stroke-width="4"/>
    <circle cx="992" cy="290" r="52" fill="#fff" stroke="#f47b20" stroke-width="4"/>
    <circle cx="200" cy="282" r="14" fill="none" stroke="#f47b20" stroke-width="5"/>
    <line x1="210" y1="292" x2="224" y2="306" stroke="#f47b20" stroke-width="6" stroke-linecap="round"/>
    <rect x="578" y="162" width="44" height="30" rx="2" fill="none" stroke="#f47b20" stroke-width="4"/>
    <line x1="600" y1="192" x2="600" y2="202" stroke="#f47b20" stroke-width="4"/>
    <line x1="588" y1="203" x2="612" y2="203" stroke="#f47b20" stroke-width="4"/>
    <circle cx="992" cy="290" r="20" fill="none" stroke="#f47b20" stroke-width="4"/>
    <circle cx="985" cy="284" r="2.5" fill="#f47b20"/><circle cx="999" cy="284" r="2.5" fill="#f47b20"/>
    <path d="M982 296 Q992 306 1002 296" fill="none" stroke="#f47b20" stroke-width="3"/>
  </svg>
  <div class="step-label" style="left:108px;top:352px">Search &amp; Find<br>Hairdresser</div>
  <div class="step-label" style="left:500px;top:242px">Book Your<br>Appointment Online</div>
  <div class="step-label" style="left:892px;top:352px">Enjoy Your<br>New Hairstyle</div>
  <div class="steps-btn">SEE HOW IT WORKS</div>
</section>

<section class="clients">
  <h2 class="clients-title">Happy Clients</h2>
  <p class="clients-sub">Lorem ipsum dolor sit amet loweeb</p>
  <svg class="arrow" style="left:40px" width="20" height="30" viewBox="0 0 20 30"><polyline points="15,4 5,15 15,26" fill="none" stroke="#c3c3c3" stroke-width="3"/></svg>
  <svg class="arrow" style="left:1140px" width="20" height="30" viewBox="0 0 20 30"><polyline points="5,4 15,15 5,26" fill="none" stroke="#c3c3c3" stroke-width="3"/></svg>
  <div class="avatar" role="img" aria-label="Portrait of a happy client"></div>
  <p class="client-name">Vestibulum porta, diam quis</p>
  <span class="quote-mark" style="left:150px">&ldquo;</span>
  <p class="quote">Lorem ipsum dolor sit amet, consectetur adipiscing elit. Integer venenatis tincidunt elit, aliquam semper quam pulvinar id. Aliquam erat volutpat. Integer nulla arcu, sagittis sed dignissim quis, tincidunt sed felis.</p>
  <span class="quote-mark" style="left:1020px">&rdquo;</span>
</section>

<section class="booking">
  <div class="booking-photo" role="img" aria-label="Soft photo of a desk calendar and pen"></div>
  <div class="form-card">
    <div class="form-row"><div class="input">Name</div><div class="input">Email Address</div></div>
    <div class="form-row"><div class="input">Phone Number</div><div class="input">Appointment Type <span>&#9662;</span></div></div>
    <div class="form-row"><div class="input">Appointment Date <span style="color:#f47b20">&#9638;</span></div><div class="input">Appointment Time <span>&#9662;</span></div></div>
    <div class="form-row"><div class="input area">Comments</div></div>
    <div class="form-row" style="margin-bottom:0"><div class="input area" style="height:50px;visibility:hidden"></div></div>
    <span class="submit">GET APPOINTMENT</span>
  </div>
  <div class="booking-cta">
    <h3>What Are You Waiting For?</h3>
    <p>Make An Appointment At<br>The Hairdresser !</p>
  </div>
</section>

<footer class="site-footer">
  <div class="fcol" style="left:130px">
    <h4>Quick Links</h4>
    <div>&rsaquo; Home</div><div>&rsaquo; About Us</div><div>&rsaquo; How It Works</div><div>&rsaquo; Testimonials</div><div>&rsaquo; Contact Us</div>
  </div>
  <div class="fcol" style="left:340px;width:240px">
    <h4>Contact Details</h4>
    <div class="row"><svg width="12" height="16" viewBox="0 0 12 16"><path d="M6 15 C3 10 1 8 1 5.5 A5 5 0 0 1 11 5.5 C11 8 9 10 6 15Z" fill="#f47b20"/></svg><span><b>TRIMTABLE,</b><br>Lindenlaan 12, 1011 AB<br>Amsterdam, Netherlands</span></div>
    <div class="row"><svg width="12" height="14" viewBox="0 0 12 14"><path d="M2 1 L5 1 L6 4 L4 5.5 Q5.5 8.5 8 10 L9.5 8 L12 9 L12 12 Q6 13 1 5 Z" fill="#f47b20"/></svg><span class="phone">(123) 456 7890</span></div>
    <div class="row"><svg width="14" height="10" viewBox="0 0 14 10"><rect x="0.5" y="0.5" width="13" height="9" fill="none" stroke="#f47b20"/><polyline points="0.5,0.5 7,6 13.5,0.5" fill="none" stroke="#f47b20"/></svg><span>info@trimtable.com</span></div>
  </div>
  <div class="fcol" style="left:600px;width:240px">
    <h4>Hours of Operations</h4>
    <div><b>Monday to Friday</b><br>10:00 am to 08:00 pm</div>
    <div style="margin-top:6px"><b>Saturday</b><br>10:00 am to 06:00 pm</div>
    <div style="margin-top:6px"><b>Sunday</b> - Closed</div>
  </div>
  <div class="fbrand"><span class="brand-square"></span><span>TrimTable</span></div>
  <div class="socials"><i></i><i></i><i></i><i></i></div>
  <p class="copy">Copyright 2015 TrimTable.<br>All Rights Reserved.<br>www.TrimTable.com</p>
</footer>

</body>
</html>
```